New Innovative Counselling and psychotherapy Service needs Business Card design

Keep it simple and professional. On one side, just company name and logo (perhaps in all blue) and maybe a tag line.

On other side (all white) my name and Qualifications in centre

Industry/Entity Type

Health And Wellness

Contact Information for Business Card

Dara Whelby
Counsellor & Psychotherapist
BSc (Psychol.), BA, Dip. (Couns. & Psych.), PG.Cert (CBT), FGTrK, ONRE

I will also require Mobile no, Email and web site address of which I'll pass on to final designer.

Font styles to use
Sans Serif

Requirements
Must have
• My Logo Only and please use the colours in logo that is in it.
Should not have
• Any other images

```html
<!DOCTYPE html>
<html lang="en">
<head>
<meta charset="utf-8">
<title>Harbor Grove — Business Card</title>
<link href="https://fonts.googleapis.com/css2?family=Roboto:wght@300;400;700&display=swap" rel="stylesheet">
<style>
  :root {
    --sky: #52b6ec;
    --sky-deep: #3fa3e0;
    --leaf: #8cc859;
    --ink: #2b2d31;
    --ink-soft: #3c3f44;
    --paper: #ffffff;
    --backdrop: #e6e7e9;
  }
  * { box-sizing: border-box; margin: 0; padding: 0; }
  html, body { width: 1200px; height: 726px; overflow: hidden; }
  body {
    background: var(--backdrop);
    font-family: "Roboto", Arial, sans-serif;
    position: relative;
  }
  .card {
    position: absolute;
    top: 208px;
    width: 540px;
    height: 310px;
    border-radius: 4px;
    overflow: hidden;
    box-shadow: 0 6px 18px rgba(0,0,0,0.12);
  }
  /* Front */
  .card-front { left: 40px; background: var(--sky); }
  .front-brand {
    position: absolute;
    left: 110px; top: 118px;
    display: flex; align-items: center; gap: 18px;
  }
  .brand-dot {
    width: 64px; height: 64px; border-radius: 50%;
    background: var(--paper);
  }
  .front-name {
    color: var(--paper);
    font-weight: 300;
    font-size: 40px;
    letter-spacing: 0.5px;
    line-height: 1;
  }
  .front-tagline {
    color: var(--paper);
    font-weight: 400;
    font-size: 13px;
    letter-spacing: 6px;
    margin-top: 8px;
  }
  /* Back */
  .card-back { left: 620px; background: var(--paper); }
  .tab { position: absolute; width: 22px; background: var(--sky-deep); }
  .tab-left { left: 0; top: 108px; height: 186px; border-radius: 0 14px 14px 0; }
  .tab-right { right: 0; top: 24px; height: 186px; border-radius: 14px 0 0 14px; }
  .holder {
    position: absolute; left: 50px; top: 116px;
  }
  .holder-name {
    color: var(--sky-deep);
    font-weight: 700;
    font-size: 22px;
    line-height: 1.1;
  }
  .holder-role, .holder-quals {
    color: var(--ink-soft);
    font-size: 10.5px;
    line-height: 1.35;
  }
  .contact-list { list-style: none; margin-top: 14px; }
  .contact-list li {
    display: flex; align-items: center; gap: 10px;
    color: var(--ink);
    font-size: 14px;
    line-height: 1.45;
  }
  .contact-list svg { width: 13px; height: 13px; flex: none; }
  .back-brand {
    position: absolute; right: 58px; top: 60px;
    display: flex; flex-direction: column; align-items: center; gap: 18px;
  }
  .back-brand .brand-dot { width: 86px; height: 86px; background: var(--sky-deep); }
  .back-name {
    color: var(--ink);
    font-weight: 300;
    font-size: 26px;
  }
</style>
</head>
<body>
  <section class="card card-front" aria-label="Card front">
    <div class="front-brand">
      <div class="brand-dot"></div>
      <div>
        <div class="front-name">Harbor Grove</div>
        <div class="front-tagline">A tag line goes here</div>
      </div>
    </div>
  </section>

  <section class="card card-back" aria-label="Card back">
    <div class="tab tab-left"></div>
    <div class="tab tab-right"></div>

    <div class="holder">
      <h1 class="holder-name">Dara Whelby</h1>
      <p class="holder-role">Counsellor &amp; Psychotherapist</p>
      <p class="holder-quals">BSc (Psychol.), BA, Dip. (Couns. &amp; Psych.),<br>PG.Cert (CBT), FGTrK, ONRE</p>
      <ul class="contact-list">
        <li>
          <svg viewBox="0 0 16 16" aria-hidden="true"><path fill="#8cc859" d="M2 6c0-2 2-3 6-3s6 1 6 3v1h-3V5.5H5V7H2z"/><rect x="3" y="8" width="10" height="6" rx="1" fill="#52b6ec"/></svg>
          0123 456 7801
        </li>
        <li>
          <svg viewBox="0 0 16 16" aria-hidden="true"><rect x="1" y="3" width="14" height="10" fill="#52b6ec"/><path d="M1 3l7 6 7-6" fill="none" stroke="#8cc859" stroke-width="1.6"/></svg>
          dara.w@HarborGrove.com
        </li>
        <li>
          <svg viewBox="0 0 16 16" aria-hidden="true"><circle cx="8" cy="8" r="7" fill="#52b6ec"/><path d="M1 8h14M8 1c3 3 3 11 0 14M8 1c-3 3-3 11 0 14" fill="none" stroke="#8cc859" stroke-width="1.2"/></svg>
          www.HarborGrove.com
        </li>
      </ul>
    </div>

    <div class="back-brand">
      <div class="brand-dot"></div>
      <div class="back-name">Harbor Grove</div>
    </div>
  </section>
</body>
</html>
```